IT Company requires new Business Card design.

Over the years we have had a few different business card designs. We are now due for new cards across the board for all staff. We felt this would be a good time to start fresh with a new design. Our traditional card simply had our details on the front, and a list of services on the back. We don't particularly need the list of services, we have had cards where the only thing on the rear of the card was our logo.
Feel free to be creative, we would like our tag line "Complete IT Management" to appear at some point, doesn't necessarily have to be with the logo.
I have attached samples and drafts of various previous cards we have used over the years.

```html
<!DOCTYPE html>
<html lang="en">
<head>
<meta charset="utf-8">
<title>Ridgeway Netcare – Business Card</title>
<link rel="stylesheet" href="https://fonts.googleapis.com/css2?family=Open+Sans:wght@400;600;700&display=swap">
<style>
  :root {
    --page-bg: #e6e6e6;
    --card-bg: #ffffff;
    --brand-slate: #5f717c;
    --swoosh-dark: #3b3b3d;
    --text-main: #4a4a4a;
    --text-soft: #5a5a5a;
    --divider: #cfcfcf;
    --on-band: #ffffff;
  }
  * { box-sizing: border-box; margin: 0; padding: 0; }
  html, body {
    width: 1034px;
    height: 1200px;
    overflow: hidden;
    background: var(--page-bg);
    font-family: "Open Sans", Arial, sans-serif;
  }
  .card {
    position: absolute;
    left: 74px;
    width: 898px;
    height: 514px;
    background: var(--card-bg);
    overflow: hidden;
    box-shadow: 0 2px 6px rgba(0,0,0,0.18);
  }
  .card--front { top: 57px; }
  .card--back  { top: 631px; }

  /* Front: brand lockup */
  .brand {
    position: absolute;
    left: 64px;
    top: 124px;
    display: flex;
    align-items: center;
    gap: 16px;
  }
  .brand__square {
    width: 62px;
    height: 62px;
    background: var(--brand-slate);
  }
  .brand__name {
    color: var(--brand-slate);
    font-weight: 700;
    font-size: 36px;
    line-height: 38px;
    letter-spacing: 0.5px;
  }
  .brand__tagline {
    position: absolute;
    left: 142px;
    top: 210px;
    color: var(--brand-slate);
    font-size: 12.5px;
    font-weight: 600;
    letter-spacing: 2.2px;
    text-transform: uppercase;
  }

  .divider {
    position: absolute;
    left: 449px;
    top: 60px;
    width: 2px;
    height: 270px;
    background: linear-gradient(to bottom, rgba(207,207,207,0), var(--divider) 20%, var(--divider) 80%, rgba(207,207,207,0));
  }

  .person {
    position: absolute;
    left: 473px;
    top: 58px;
  }
  .person__name {
    color: var(--brand-slate);
    font-weight: 700;
    font-size: 27px;
    line-height: 34px;
  }
  .person__role {
    color: var(--text-soft);
    font-size: 21px;
    line-height: 30px;
  }

  .contacts {
    position: absolute;
    left: 473px;
    top: 145px;
    list-style: none;
  }
  .contacts__item {
    display: flex;
    align-items: center;
    gap: 10px;
    height: 35px;
    color: var(--text-main);
    font-size: 21px;
  }
  .contacts__icon {
    width: 20px;
    height: 20px;
    flex: none;
  }

  .wave {
    position: absolute;
    left: 0;
    top: 0;
    width: 898px;
    height: 514px;
  }
  .address {
    position: absolute;
    left: 0;
    top: 460px;
    width: 523px;
    text-align: center;
    color: var(--on-band);
    font-size: 21px;
  }

  /* Back */
  .back-brand {
    position: absolute;
    left: 0;
    top: 180px;
    width: 100%;
    display: flex;
    justify-content: center;
    align-items: center;
    gap: 26px;
  }
  .back-brand__square {
    width: 110px;
    height: 110px;
    background: var(--brand-slate);
  }
  .back-brand__name {
    color: var(--brand-slate);
    font-weight: 700;
    font-size: 56px;
    line-height: 58px;
    letter-spacing: 1px;
  }
  .back-url {
    position: absolute;
    left: 0;
    top: 462px;
    width: 100%;
    text-align: center;
    color: #333;
    font-size: 25px;
    letter-spacing: 2px;
  }
</style>
</head>
<body>

<section class="card card--front" aria-label="Business card front">
  <div class="brand">
    <div class="brand__square"></div>
    <div class="brand__name">RIDGEWAY<br>NETCARE</div>
  </div>
  <div class="brand__tagline">Complete IT Management</div>

  <div class="divider"></div>

  <div class="person">
    <div class="person__name">Daniel Marsh</div>
    <div class="person__role">Operation Manager</div>
  </div>

  <ul class="contacts">
    <li class="contacts__item">
      <svg class="contacts__icon" viewBox="0 0 20 20" aria-hidden="true">
        <circle cx="10" cy="10" r="8.5" fill="none" stroke="#555" stroke-width="1.4"/>
        <path d="M7 5.5c-1 1-1 3 1 5.5s4 3 5 2l-1.5-1.8-1.3.6c-.9-.4-2-1.8-2.3-2.7l.8-1.2z" fill="#555"/>
      </svg>
      08 5550 1842
    </li>
    <li class="contacts__item">
      <svg class="contacts__icon" viewBox="0 0 20 20" aria-hidden="true">
        <rect x="6" y="2" width="8" height="16" rx="1.5" fill="#555"/>
        <rect x="7.3" y="4" width="5.4" height="5" fill="#fff"/>
        <rect x="7.3" y="10.5" width="5.4" height="5" fill="#ddd"/>
      </svg>
      0400 555 719
    </li>
    <li class="contacts__item">
      <svg class="contacts__icon" viewBox="0 0 20 20" aria-hidden="true">
        <rect x="5" y="3" width="10" height="6" fill="#555"/>
        <rect x="2" y="9" width="16" height="8" rx="1.5" fill="#555"/>
        <rect x="5" y="11" width="10" height="2" fill="#fff"/>
      </svg>
      08 5550 1842
    </li>
    <li class="contacts__item">
      <svg class="contacts__icon" viewBox="0 0 20 20" aria-hidden="true">
        <rect x="2" y="5" width="16" height="11" fill="#555"/>
        <path d="M2.5 5.5 10 11l7.5-5.5" fill="none" stroke="#fff" stroke-width="1.3"/>
      </svg>
      daniel@ridgewaynetcare.com.au
    </li>
    <li class="contacts__item">
      <svg class="contacts__icon" viewBox="0 0 20 20" aria-hidden="true">
        <circle cx="10" cy="10" r="8" fill="none" stroke="#555" stroke-width="1.4"/>
        <ellipse cx="10" cy="10" rx="3.5" ry="8" fill="none" stroke="#555" stroke-width="1.2"/>
        <path d="M2 10h16M3.5 6h13M3.5 14h13" stroke="#555" stroke-width="1.1"/>
      </svg>
      www.ridgewaynetcare.com.au
    </li>
  </ul>

  <svg class="wave" viewBox="0 0 898 514" aria-hidden="true">
    <path d="M0 384 C 140 410, 240 448, 380 440 C 560 430, 700 378, 898 372 L 898 514 L 0 514 Z" fill="var(--brand-slate)"/>
    <path d="M0 364 C 150 408, 250 432, 380 428 C 560 420, 700 372, 898 360 C 700 366, 560 410, 380 418 C 250 424, 140 398, 0 372 Z" fill="var(--swoosh-dark)"/>
  </svg>

  <div class="address">Unit 4 12 Banksia Road, Kelmscott WA 6111</div>
</section>

<section class="card card--back" aria-label="Business card back">
  <div class="back-brand">
    <div class="back-brand__square"></div>
    <div class="back-brand__name">RIDGEWAY<br>NETCARE</div>
  </div>
  <div class="back-url">www.ridgewaynetcare.com.au</div>
</section>

</body>
</html>
```